Medical Billing Company Needs a Business Card Design

We need a business card design for a Florida based medical billing company called 'Clinicians Keystone Solutions'. We specialize in providing revenue cycle management services to physician and therapist offices (we're basically their back-office processing partner for providing billing software, claims submissions, A/R follow-up and patient statements & collections. Our logo is red and blue-ish, so make sure that whatever other elements are used will match appropriately. Our current business card design has a too small font size. I'd like to project an image that shows we are modern & reliable. On a side note, I'm planning on using ZUB for printing these cards.

Target Market(s)

Office managers, physicians, therapists

Industry/Entity Type

Printing

Requirements
Must have
• Logo
Name of Employee
Phone
Fax
E-mail
Website

```html
<!DOCTYPE html>
<html lang="en">
<head>
<meta charset="utf-8">
<title>Clinicians Keystone Solutions – Business Card</title>
<link href="https://fonts.googleapis.com/css2?family=Lato:wght@400;700&family=Montserrat:wght@500&display=swap" rel="stylesheet">
<style>
  :root {
    --backdrop: #e9e7e3;
    --card: #ffffff;
    --navy: #25237a;
    --violet-top: #6a5fbf;
    --violet-bottom: #1f1878;
    --crimson: #b8262c;
    --ink: #444444;
    --band-text: #ffffff;
  }
  * { box-sizing: border-box; margin: 0; padding: 0; }
  html, body { width: 1200px; height: 720px; overflow: hidden; }
  body {
    background: var(--backdrop);
    font-family: "Lato", Arial, sans-serif;
    position: relative;
  }
  .card {
    position: absolute;
    top: 205px;
    width: 540px;
    height: 309px;
    background: var(--card);
    box-shadow: 0 6px 18px rgba(0,0,0,0.12);
    overflow: hidden;
  }
  .card--front { left: 40px; }
  .card--back { left: 620px; }

  .wordmark {
    font-family: "Montserrat", Arial, sans-serif;
    font-weight: 500;
    color: var(--navy);
    letter-spacing: 2px;
    white-space: nowrap;
    display: flex;
    align-items: center;
    gap: 10px;
  }
  .wordmark__mark {
    width: 14px; height: 14px;
    background: var(--crimson);
    flex: none;
  }
  .card--front .wordmark {
    position: absolute;
    top: 52px; left: 0; right: 0;
    justify-content: center;
    font-size: 25px;
  }

  .rule {
    position: absolute;
    left: 0; right: 0;
    top: 124px;
    height: 8px;
    border-top: 2px solid var(--crimson);
    border-bottom: 2px solid var(--crimson);
  }
  .band {
    position: absolute;
    left: 0; right: 0; top: 132px; bottom: 0;
    background: linear-gradient(180deg, var(--violet-top) 0%, var(--violet-bottom) 100%);
  }
  .holder {
    position: absolute;
    top: 16px; left: 0; right: 0;
    text-align: center;
    font-size: 21px;
    font-weight: 700;
    color: var(--band-text);
  }
  .holder__title { font-weight: 400; color: #f3c9cc; }

  .address {
    position: absolute;
    top: 76px; right: 290px;
    text-align: right;
    font-size: 14px;
    line-height: 21px;
    color: var(--band-text);
  }
  .divider {
    position: absolute;
    left: 264px; top: 64px;
    width: 1px; height: 92px;
    background: rgba(255,255,255,0.7);
  }
  .contacts {
    position: absolute;
    top: 60px; left: 280px;
    list-style: none;
    font-size: 14px;
    line-height: 24px;
    color: var(--band-text);
  }
  .contacts li { display: flex; align-items: center; gap: 8px; }
  .contacts svg { width: 13px; height: 13px; flex: none; }

  .card--back .wordmark {
    position: absolute;
    top: 112px; left: 0; right: 0;
    justify-content: center;
    font-size: 29px;
  }
  .web {
    position: absolute;
    bottom: 62px; left: 0; right: 0;
    text-align: center;
    font-size: 16px;
    letter-spacing: 4px;
    color: var(--ink);
  }
</style>
</head>
<body>

<section class="card card--front" aria-label="Card front">
  <div class="wordmark"><span class="wordmark__mark"></span>CLINICIANS KEYSTONE</div>
  <div class="rule"></div>
  <div class="band">
    <p class="holder">Your Name, <span class="holder__title">Title</span></p>
    <address class="address" style="font-style:normal">
      Street Name<br>City Name<br>State Zip Code
    </address>
    <div class="divider"></div>
    <ul class="contacts">
      <li>
        <svg viewBox="0 0 16 16" aria-hidden="true"><path fill="#fff" d="M3.5 1.5l2.5 0 1 3.5-1.8 1.2a9 9 0 0 0 4.6 4.6L11 9l3.5 1v2.5c0 1-1 2-2 2A11 11 0 0 1 1.5 3.5c0-1 1-2 2-2z"/></svg>
        123-456-0789
      </li>
      <li>
        <svg viewBox="0 0 16 16" aria-hidden="true"><rect x="4" y="1" width="8" height="5" fill="none" stroke="#fff" stroke-width="1.5"/><rect x="1.5" y="6" width="13" height="7" rx="1" fill="#fff"/><rect x="4" y="11" width="8" height="4" fill="#fff"/></svg>
        123-456-0789
      </li>
      <li>
        <svg viewBox="0 0 16 16" aria-hidden="true"><rect x="1" y="3" width="14" height="10" rx="1" fill="#fff"/><path d="M1.5 3.8L8 9l6.5-5.2" fill="none" stroke="#3a3096" stroke-width="1.3"/></svg>
        info@clinicianskeystone.com
      </li>
      <li>
        <svg viewBox="0 0 16 16" aria-hidden="true"><circle cx="8" cy="8" r="6.5" fill="none" stroke="#fff" stroke-width="1.4"/><ellipse cx="8" cy="8" rx="2.8" ry="6.5" fill="none" stroke="#fff" stroke-width="1.2"/><path d="M1.5 8h13" stroke="#fff" stroke-width="1.2"/></svg>
        www.clinicianskeystone.com
      </li>
    </ul>
  </div>
</section>

<section class="card card--back" aria-label="Card back">
  <div class="wordmark"><span class="wordmark__mark"></span>CLINICIANS KEYSTONE</div>
  <p class="web">www.clinicianskeystone.com</p>
</section>

</body>
</html>
```